KRT Engineering Business Card Design

We’re looking for an elegant, clean, and timeless business card design that communicates experience, capability, and reliability.

KRT Engineering was established in 1995 , we are a Government Contracting company providing Professional Services to the Office of Frontier Affairs, Harbor Protection and the Vantage Collective. Our capabilities include: Acquisition & Program Management; Intelligence & Security Operations; Cyber, IT & Network Operations; Lifecycle Logistics & Asset Readiness; C5ISR Systems Engineering & Sustainment.

We want the card to reflect a straightforward, confident approach to business. The design should feel polished and professional without being flashy or overly corporate.

Design Direction
Clean, sophisticated, and uncluttered
Elegant but understated
Strong typography and thoughtful spacing
A timeless aesthetic rather than something overly trendy
Confident and established, with a sense of substance
Easy to read and practical in a real-world business setting

The overall impression should be: “These are experienced professionals who know what they’re doing, do what they say, and can be relied upon.”

We’re open to creative interpretations. The finished card should feel distinctive through its typography, proportions, layout, and attention to detail rather than through excessive graphics or visual effects.

We’re looking for a design that would make a potential client immediately feel that they’re dealing with a capable, trustworthy, and established company.

Company Colors: Navy and Gold/Yellow (but you do not need to use these colors on the card)
Company Name: KRT Engineering Associates, Inc. (known as KRT Engineering)
Website: krtengineering.com
Company Logo: Navy & Gold (other variations attached)

```html
<!DOCTYPE html>
<html lang="en">
<head>
<meta charset="utf-8">
<title>KRT Engineering Business Card</title>
<link href="https://fonts.googleapis.com/css2?family=Poppins:wght@400;500;600;700&display=swap" rel="stylesheet">
<style>
  :root {
    --navy: #1c2a6b;
    --navy-deep: #141d52;
    --navy-light: #1f3f8a;
    --gold: #fde154;
    --white: #ffffff;
    --backdrop: #979797;
    --rule: #c9ccd8;
  }
  * { margin: 0; padding: 0; box-sizing: border-box; }
  html, body { width: 1200px; height: 1200px; overflow: hidden; }
  body {
    background: var(--backdrop);
    font-family: "Poppins", sans-serif;
    color: var(--navy);
    position: relative;
  }
  .card {
    position: absolute;
    left: 167px;
    width: 865px;
    height: 495px;
    background: var(--white);
    overflow: hidden;
  }
  .card--front { top: 73px; }
  .card--back { top: 619px; height: 494px; }
  .card__art { position: absolute; inset: 0; width: 100%; height: 100%; }
  .abs { position: absolute; white-space: nowrap; }

  /* Front */
  .wordmark { left: 114px; top: 100px; font-size: 78px; font-weight: 700; line-height: 1; letter-spacing: -1px; color: var(--navy); }
  .company-name { left: 84px; top: 228px; font-size: 26px; font-weight: 600; letter-spacing: -0.2px; }
  .gold-rule { height: 3px; background: var(--gold); }
  .front-rule { left: 85px; top: 267px; width: 191px; }
  .tagline { left: 85px; top: 280px; font-size: 18px; font-weight: 400; line-height: 22px; white-space: normal; width: 340px; }
  .established { left: 85px; top: 346px; font-size: 17px; font-weight: 600; letter-spacing: 3.4px; padding-left: 7px; border-left: 2px solid var(--gold); line-height: 20px; }
  .front-web { left: 86px; top: 400px; font-size: 19px; font-weight: 600; letter-spacing: 3.3px; }

  /* Back */
  .person-name { left: 155px; top: 150px; font-size: 27px; font-weight: 700; line-height: 1.2; }
  .person-title { left: 157px; top: 182px; font-size: 16px; font-weight: 500; letter-spacing: 1.2px; }
  .back-rule { left: 157px; top: 210px; width: 81px; height: 2px; }
  .contact { left: 158px; }
  .contact__icon { position: absolute; left: 0; width: 18px; height: 18px; }
  .contact__text { position: absolute; left: 30px; font-size: 13.5px; font-weight: 500; line-height: 17px; white-space: nowrap; }
  .back-company { left: 158px; top: 383px; font-size: 15px; font-weight: 600; }
  .divider { left: 478px; top: 156px; width: 1px; height: 253px; background: var(--rule); }

  .cap-head { left: 512px; top: 152px; display: flex; align-items: center; gap: 13px; }
  .cap-head__badge { width: 34px; height: 34px; }
  .cap-head__label { font-size: 16px; font-weight: 600; letter-spacing: 0.4px; }
  .cap-list { position: absolute; left: 516px; top: 195px; width: 308px; list-style: none; }
  .cap-item { display: flex; align-items: center; gap: 17px; border-bottom: 1px solid var(--rule); height: 43px; font-size: 14px; font-weight: 500; line-height: 16px; }
  .cap-item:first-child { height: 45px; }
  .cap-item:last-child { border-bottom: none; height: 45px; }
  .cap-item svg { width: 26px; height: 26px; flex: none; }
</style>
</head>
<body>

<section class="card card--front">
  <svg class="card__art" viewBox="0 0 865 495" aria-hidden="true">
    <defs>
      <linearGradient id="navyFront" x1="0" y1="0" x2="1" y2="1">
        <stop offset="0" stop-color="#141d52"/>
        <stop offset="0.55" stop-color="#1c3a86"/>
        <stop offset="1" stop-color="#141d52"/>
      </linearGradient>
    </defs>
    <rect width="865" height="495" fill="url(#navyFront)"/>
    <path d="M0,0 H552 C690,75 780,230 745,390 C737,430 722,465 700,495 H0 Z" fill="#ffffff"/>
    <path d="M590,37 C700,130 760,260 722,400 C710,445 695,472 684,495 H634 C670,440 705,360 707,287 C708,200 670,110 590,37 Z" fill="#fde154"/>
  </svg>
  <div class="abs wordmark">KRT</div>
  <h1 class="abs company-name">KRT ENGINEERING ASSOCIATES, INC.</h1>
  <div class="abs gold-rule front-rule"></div>
  <p class="abs tagline">Professional Services for Defense,<br>Security &amp; Intelligence</p>
  <p class="abs established">ESTABLISHED 1995</p>
  <p class="abs front-web">www.krtengineering.com</p>
</section>

<section class="card card--back">
  <svg class="card__art" viewBox="0 0 865 494" aria-hidden="true">
    <defs>
      <linearGradient id="navyBack" x1="1" y1="0" x2="0" y2="1">
        <stop offset="0" stop-color="#141d52"/>
        <stop offset="0.5" stop-color="#1c3a86"/>
        <stop offset="1" stop-color="#141d52"/>
      </linearGradient>
    </defs>
    <rect width="865" height="494" fill="url(#navyBack)"/>
    <path d="M233,0 H865 V494 H86 C40,420 18,340 42,260 C75,150 150,60 233,0 Z" fill="#ffffff"/>
    <path d="M193,37 C110,110 45,210 47,300 C49,380 80,440 100,494 H153 C110,430 76,370 76,300 C76,200 120,110 193,37 Z" fill="#fde154"/>
  </svg>

  <h2 class="abs person-name">Maren Castell, P.E.</h2>
  <p class="abs person-title">President, CEO, &amp; Founder</p>
  <div class="abs gold-rule back-rule"></div>

  <div class="abs contact" style="top:233px">
    <svg class="contact__icon" viewBox="0 0 18 18" aria-hidden="true"><circle cx="9" cy="9" r="9" fill="#fde154"/><path d="M6.2 4.6l1.4 2-.9 1.1c.6 1.3 1.5 2.2 2.7 2.8l1.1-.9 2 1.4-.7 1.6c-3.4 0-6.8-3.4-6.9-6.9z" fill="#e8b92e"/></svg>
    <span class="contact__text" style="top:0">555-014-2287</span>
  </div>
  <div class="abs contact" style="top:264px">
    <svg class="contact__icon" viewBox="0 0 18 18" aria-hidden="true"><circle cx="9" cy="9" r="9" fill="#fde154"/><path d="M9 3.8a3.4 3.4 0 0 0-3.4 3.4c0 2.5 3.4 6.2 3.4 6.2s3.4-3.7 3.4-6.2A3.4 3.4 0 0 0 9 3.8z" fill="#ffffff"/><circle cx="9" cy="7.2" r="1.3" fill="#e8b92e"/></svg>
    <span class="contact__text" style="top:0">4120 Alder Street, Suite 310,<br>Harbor City, VA 23999</span>
  </div>
  <div class="abs contact" style="top:308px">
    <svg class="contact__icon" viewBox="0 0 18 18" aria-hidden="true"><circle cx="9" cy="9" r="9" fill="#fde154"/><rect x="4.6" y="5.8" width="8.8" height="6.4" rx="1" fill="none" stroke="#e8b92e" stroke-width="1.1"/><path d="M4.8 6.2L9 9.3l4.2-3.1" fill="none" stroke="#e8b92e" stroke-width="1.1"/></svg>
    <span class="contact__text" style="top:0">Maren@krtengineering.com</span>
  </div>
  <div class="abs contact" style="top:343px">
    <svg class="contact__icon" viewBox="0 0 18 18" aria-hidden="true"><circle cx="9" cy="9" r="9" fill="#fde154"/><g fill="none" stroke="#e8b92e" stroke-width="1"><circle cx="9" cy="9" r="4.6"/><ellipse cx="9" cy="9" rx="2" ry="4.6"/><path d="M4.4 9h9.2M5 6.7h8M5 11.3h8"/></g></svg>
    <span class="contact__text" style="top:0">www.krtengineering.com</span>
  </div>

  <p class="abs back-company">KRT ENGINEERING ASSOCIATES, INC.</p>
  <div class="abs divider"></div>

  <div class="abs cap-head">
    <svg class="cap-head__badge" viewBox="0 0 34 34" aria-hidden="true"><circle cx="17" cy="17" r="17" fill="#1c2a6b"/><g stroke="#fde154" stroke-width="1.4" fill="none"><circle cx="17" cy="17" r="4.5"/><path d="M17 6v6.5M17 21.5V28M6 17h6.5M21.5 17H28M9.2 9.2l4.6 4.6M20.2 20.2l4.6 4.6M24.8 9.2l-4.6 4.6M13.8 20.2l-4.6 4.6"/></g></svg>
    <span class="cap-head__label">CAPABILITIES</span>
  </div>

  <ul class="cap-list">
    <li class="cap-item">
      <svg viewBox="0 0 26 26" aria-hidden="true"><path d="M2 15l5-4 4 2 4-2 4 1 5 3-3 3-5-2-4 3-4-1z" fill="#e8c23a"/><rect x="4" y="3" width="4" height="4" fill="#e8c23a"/><rect x="17" y="3" width="5" height="4" fill="#e8c23a"/></svg>
      <span>Acquisition &amp; Program<br>Management</span>
    </li>
    <li class="cap-item">
      <svg viewBox="0 0 26 26" aria-hidden="true"><circle cx="10" cy="13" r="8" fill="#e8c23a"/><g stroke="#e8c23a" stroke-width="1.4"><path d="M18 8h5M18 13h6M18 18h5"/></g><circle cx="10" cy="13" r="2.5" fill="#fff"/></svg>
      <span>Intelligence &amp; Security Operations</span>
    </li>
    <li class="cap-item">
      <svg viewBox="0 0 26 26" aria-hidden="true"><circle cx="13" cy="8" r="5" fill="#e8c23a"/><rect x="7" y="14" width="12" height="7" rx="1" fill="#e8c23a"/><path d="M3 22h20" stroke="#e8c23a" stroke-width="1.6"/></svg>
      <span>Cyber, IT &amp; Network Operations</span>
    </li>
    <li class="cap-item">
      <svg viewBox="0 0 26 26" aria-hidden="true"><rect x="3" y="12" width="11" height="8" fill="#e8c23a"/><circle cx="6" cy="22" r="2" fill="#e8c23a"/><circle cx="12" cy="22" r="2" fill="#e8c23a"/><path d="M19 3a3.5 3.5 0 0 0-3.5 3.5c0 2.4 3.5 5.5 3.5 5.5s3.5-3.1 3.5-5.5A3.5 3.5 0 0 0 19 3z" fill="none" stroke="#e8c23a" stroke-width="1.4"/></svg>
      <span>Lifecycle Logistics &amp; Asset Readiness</span>
    </li>
    <li class="cap-item">
      <svg viewBox="0 0 26 26" aria-hidden="true"><circle cx="9" cy="15" r="6" fill="none" stroke="#e8c23a" stroke-width="3.4" stroke-dasharray="3 1.6"/><circle cx="19" cy="8" r="3.6" fill="none" stroke="#e8c23a" stroke-width="2.4" stroke-dasharray="2 1.2"/><circle cx="19" cy="20" r="3" fill="none" stroke="#e8c23a" stroke-width="2.2"/></svg>
      <span>C5ISR Systems Engineering<br>&amp; Sustainment</span>
    </li>
  </ul>
</section>

</body>
</html>
```